Professional Package for CPA Firm

We would like a stationery design for our new CPA Firm based in Atlanta, GA called 'Vale 8'. We work with investors to help grow investments, tax free. We would like the design to have a professional/minimal look with a 'wow' factor. We need 9.5″ x 4.125″, 9x12, and 10x13 mailing envelopes, business cards, and a letterhead. We have a logo that is already complete. For the letterhead, we would like to have space to put credentials at the bottom of the page

Industry/Entity Type

CPA, Accounting

```html
<!DOCTYPE html>
<html lang="en">
<head>
<meta charset="utf-8">
<title>Vale 8 — Business Card</title>
<link href="https://fonts.googleapis.com/css2?family=Open+Sans:wght@400;600&display=swap" rel="stylesheet">
<style>
  :root {
    --page-bg: #d9d6d1;
    --navy: #1b2937;
    --navy-deep: #121c26;
    --teal: #1f7d88;
    --teal-text: #1a6a74;
    --red: #e2323b;
    --cream: #f1ece4;
    --frost-top: #eeece8;
    --frost-bottom: #d8d4cf;
    --ink: #2a2f35;
  }
  html, body {
    margin: 0;
    width: 1200px;
    height: 969px;
    overflow: hidden;
    background: var(--page-bg);
    font-family: "Open Sans", Arial, sans-serif;
  }
  .business-card {
    position: absolute;
    left: 100px;
    top: 200px;
    width: 1000px;
    height: 569px;
    border-radius: 26px;
    overflow: hidden;
    background: linear-gradient(160deg, var(--frost-top), var(--frost-bottom));
    box-shadow: 0 18px 40px rgba(0,0,0,0.18);
  }
  .card-art { position: absolute; inset: 0; }
  .brand {
    position: absolute;
    left: 120px;
    top: 238px;
    color: var(--cream);
  }
  .brand-name {
    font-size: 68px;
    font-weight: 600;
    letter-spacing: 3px;
    line-height: 1;
    margin: 0;
  }
  .brand-tagline {
    margin: 14px 0 0 2px;
    font-size: 18px;
    font-weight: 400;
    letter-spacing: 2.6px;
  }
  .contact {
    position: absolute;
    right: 64px;
    top: 250px;
    text-align: right;
    color: var(--ink);
  }
  .person-name {
    margin: 0;
    font-size: 31px;
    font-weight: 600;
    color: var(--teal-text);
    line-height: 1.1;
  }
  .person-title {
    margin: 2px 0 0;
    font-size: 22px;
    color: var(--red);
  }
  .address {
    margin: 18px 0 0;
    font-size: 22px;
    line-height: 28px;
    font-style: normal;
  }
  .contact-list {
    list-style: none;
    margin: 16px -28px 0 0;
    padding: 0;
    font-size: 22px;
    line-height: 29px;
  }
  .contact-list li { display: flex; justify-content: flex-end; align-items: center; gap: 10px; }
  .contact-icon { width: 17px; height: 17px; fill: var(--red); }
</style>
</head>
<body>
  <div class="business-card">
    <svg class="card-art" viewBox="0 0 1000 569" preserveAspectRatio="none" aria-hidden="true">
      <defs>
        <linearGradient id="navyFill" x1="0" y1="0" x2="1" y2="1">
          <stop offset="0" stop-color="#24313f"/>
          <stop offset="1" stop-color="#121c26"/>
        </linearGradient>
      </defs>
      <path class="wave-red" fill="#e2323b"
        d="M0,0 H1000 V219 C930,174 860,154 800,169 C620,214 420,534 210,511 C120,501 50,454 0,418 Z"/>
      <path class="wave-teal" fill="#1f7d88"
        d="M0,0 H1000 V212 C930,167 860,147 800,162 C620,207 420,527 210,504 C120,494 50,447 0,411 Z"/>
      <path class="dark-field" fill="url(#navyFill)"
        d="M0,0 H1000 V205 C930,160 860,140 800,155 C620,200 420,520 210,497 C120,487 50,440 0,404 Z"/>
    </svg>

    <div class="brand">
      <p class="brand-name">VALE 8</p>
      <p class="brand-tagline">CPAs and Tax Advisors</p>
    </div>

    <div class="contact">
      <p class="person-name">DANIEL HART</p>
      <p class="person-title">President</p>
      <address class="address">2140 Larkspur Court<br>Atlanta, Georgia 30318</address>
      <ul class="contact-list">
        <li>404-555-0172
          <svg class="contact-icon" viewBox="0 0 16 16"><path d="M3 1l3 3-1.5 2c1 2 2.5 3.5 4.5 4.5L11 9l3 3-2 2.5C6 14 2 10 1.5 3.5Z"/></svg>
        </li>
        <li>404-555-0139
          <svg class="contact-icon" viewBox="0 0 16 16"><path d="M4 0h8v16H4Zm1.5 1.5v11h5v-11Z" fill-rule="evenodd"/></svg>
        </li>
        <li>info@vale8.com
          <svg class="contact-icon" viewBox="0 0 16 16"><path d="M1 3h14v10H1Zm1 1 6 5 6-5Z" fill-rule="evenodd"/></svg>
        </li>
        <li>www.vale8.com
          <svg class="contact-icon" viewBox="0 0 16 16"><circle cx="8" cy="8" r="7.5"/></svg>
        </li>
      </ul>
    </div>
  </div>
</body>
</html>
```